Business Card Design

We need a design for business cards for our company. We have a logo. We teach EMT's and we are based out of Virginia. The information that will need to add would be, name, title, phone number, email, address. On the back of the business card would be "Train today, respond tomorrow"

Target Market(s)

People that want to become EMT's

Colors

Designer to choose colors to be used in the design.

Requirements
Must have
• company logo

```html
<!DOCTYPE html>
<html lang="en">
<head>
<meta charset="utf-8">
<title>Rescue Ready Academy – Business Card</title>
<link rel="stylesheet" href="https://fonts.googleapis.com/css2?family=Montserrat:wght@500;600;700&family=Open+Sans:wght@400;600&display=swap">
<style>
  :root{
    --stage:#2e2e2f;
    --paper:#ffffff;
    --red:#be1e2d;
    --grey:#939598;
    --ink:#3a3a3c;
    --rule:#d9d9db;
    --watermark:#f3f3f4;
  }
  *{box-sizing:border-box;margin:0;padding:0}
  html,body{width:1200px;height:866px;overflow:hidden}
  body{background:var(--stage);display:flex;flex-direction:column;align-items:center;justify-content:center;gap:40px;font-family:"Open Sans",sans-serif;color:var(--ink)}
  .card{position:relative;width:640px;height:366px;background:var(--paper);box-shadow:0 10px 24px rgba(0,0,0,.45);overflow:hidden}

  /* front */
  .card--front{border-bottom:10px solid var(--red)}
  .watermark{position:absolute;left:190px;top:40px;width:230px;height:230px;background:var(--watermark);border-radius:50%}
  .holder{position:absolute;left:48px;top:108px}
  .holder__name{font-family:"Montserrat",sans-serif;font-weight:700;font-size:24px;letter-spacing:.5px;color:var(--red);text-transform:uppercase;line-height:1}
  .holder__title{font-size:16px;color:var(--ink);margin-top:6px}
  .contact{list-style:none;margin-top:16px;font-size:16px}
  .contact li{display:flex;align-items:center;gap:8px;line-height:1.55}
  .contact svg{width:16px;height:16px;fill:var(--red);flex:none}
  .divider{position:absolute;left:48px;right:48px;top:246px;height:1px;background:var(--rule)}
  .brand{position:absolute;right:44px;top:96px;display:flex;align-items:center;gap:12px}
  .brand__dot{width:18px;height:18px;border-radius:50%;background:var(--red);flex:none}
  .brand__name{font-family:"Montserrat",sans-serif;font-weight:700;font-size:26px;color:var(--red);letter-spacing:.5px;text-transform:uppercase;line-height:1.05}
  .brand__tagline{font-family:"Montserrat",sans-serif;font-weight:600;font-size:12px;color:var(--grey);letter-spacing:.8px;text-transform:uppercase;margin-top:8px}
  .address{position:absolute;right:48px;top:264px;text-align:right;font-size:16px;line-height:1.45;color:var(--ink);font-style:normal}

  /* back */
  .card--back{background:var(--red)}
  .back__upper{position:absolute;left:0;right:0;top:0;height:46%;background:var(--grey)}
  .back__mark{position:absolute;left:50%;top:50%;width:330px;height:230px;transform:translate(-50%,-50%);background:linear-gradient(180deg,#fafafa,#eeeeee)}
</style>
</head>
<body>

<section class="card card--front">
  <div class="watermark" role="img" aria-label="faint brand decoration in the background"></div>

  <div class="holder">
    <p class="holder__name">Daniel Porter</p>
    <p class="holder__title">Managing Director</p>
    <ul class="contact">
      <li>
        <svg viewBox="0 0 24 24" aria-hidden="true"><path d="M6.6 10.8a15.1 15.1 0 0 0 6.6 6.6l2.2-2.2a1 1 0 0 1 1-.25 11.4 11.4 0 0 0 3.6.57 1 1 0 0 1 1 1V20a1 1 0 0 1-1 1A17 17 0 0 1 3 4a1 1 0 0 1 1-1h3.5a1 1 0 0 1 1 1c0 1.25.2 2.45.57 3.6a1 1 0 0 1-.25 1z"/></svg>
        044-555 010 234
      </li>
      <li>
        <svg viewBox="0 0 24 24" aria-hidden="true"><path d="M2 5h20v14H2z M4 7v.5l8 5.5 8-5.5V7l-8 5.5z" fill-rule="evenodd"/></svg>
        hello@rescueready.com
      </li>
    </ul>
  </div>

  <div class="brand">
    <span class="brand__dot"></span>
    <div>
      <p class="brand__name">Rescue Ready<br>Academy</p>
      <p class="brand__tagline">Train today, respond tomorrow</p>
    </div>
  </div>

  <div class="divider"></div>

  <address class="address">
    12 Harbor Lane, Suite 4<br>23450, Virginia
  </address>
</section>

<section class="card card--back">
  <div class="back__upper"></div>
  <div class="back__mark" role="img" aria-label="large white brand emblem area with a red pulse motif"></div>
</section>

</body>
</html>
```